Varelko App for Smart Devices IoT WiFi Electronic

Varelko is a siren manufacturer. This application is used for the company's products that have a Wi-Fi connection and an internet connection, which can be configured and activated remotely through this application. In addition, this application is used to activate the siren at specific times for the start and end of shifts in companies and schools. Users will be siren installers and IT or HR managers.
In addition to activating motorized sirens timers, some siren models have speakers and allow you to play TTS (text to speech) audio, audio recorded by the user on the phone and upload audio (mp3) with playlist programming with start and end times.
Application screens: home with dashboard (one dashboard for each category). Device categories: timers, speakers, motorized siren. Screen for requesting evaluation in the Play Store. Screen for registering the user profile. Screen for registering devices according to their category (timers, speakers, motorized siren). Screen for registering device groups. Screen for pairing the device on the client's Wi-Fi network. Screen for registering activation times. Screen for uploading MP3 audios. Screen for registering playlists with audio selection, start and end times. Screen for recording audio for later sending to the speakers. Screen for converting text to speech and sending to the speakers. It is important to have a time picker with the day of the week to program the activation times and playlist.

Target Market(s)

Schools, Companies and Stores.

Industry/Entity Type

IoT

Font styles to use
Sans Serif
Other font styles liked:
• roboto

Colors
FFC000
F8CF3A
FAE287
FDF2CF
FEFAEE

Requirements
Must have
• time picker with weekdays for timer programming feature.
Nice to have
• app review request screen on play store

```html
<!DOCTYPE html>
<html lang="en">
<head>
<meta charset="utf-8">
<title>Varelko — App Screens</title>
<link rel="stylesheet" href="https://fonts.googleapis.com/css2?family=Poppins:ital,wght@0,400;0,500;0,600;0,700;0,800;1,800&display=swap">
<style>
  :root{
    --yellow:#FFC000;
    --yellow-soft:#F8CF3A;
    --yellow-pale:#FAE287;
    --yellow-cream:#FDF2CF;
    --yellow-ivory:#FEFAEE;
    --page:#E6EAF2;
    --ink:#4A5468;
    --ink-soft:#5B6478;
    --muted:#A7ADBB;
    --line:#E4E7EE;
    --white:#FFFFFF;
  }
  *{box-sizing:border-box;margin:0;padding:0}
  html,body{width:1200px;height:3250px;overflow:hidden}
  body{position:relative;background:var(--page);font-family:"Poppins",sans-serif;color:var(--ink)}

  .backdrop{position:absolute;left:0;top:0;width:1200px;height:3250px}
  .brand-title{position:absolute;top:52px;left:0;width:1200px;text-align:center;font:600 140px/1 "Poppins",sans-serif;color:var(--yellow);letter-spacing:2px}
  .section-label{position:absolute;font:700 44px/1 "Poppins",sans-serif;color:var(--ink)}

  .screen{position:absolute;width:302px;height:655px;background:var(--white);border-radius:38px;overflow:hidden;box-shadow:0 34px 60px rgba(120,140,185,.35)}
  .screen.tinted{background:#F7F8FB}
  .status{position:absolute;top:14px;left:24px;right:22px;display:flex;justify-content:space-between;align-items:center;font:600 11px "Poppins",sans-serif;color:var(--ink);z-index:3}
  .status.light{color:var(--ink)}
  .status-icons{display:flex;gap:4px;align-items:center}
  .status-icons span{display:block;background:currentColor;border-radius:1px}

  .abs{position:absolute}
  .card{position:absolute;background:var(--white);border-radius:14px;box-shadow:0 10px 24px rgba(120,135,170,.14)}
  .field{position:absolute;height:34px;border:1px solid var(--line);border-radius:17px;display:flex;justify-content:space-between;align-items:center;padding:0 16px;font:500 9px "Poppins",sans-serif;color:var(--ink);background:var(--white)}
  .field .hint{font-size:7px;color:var(--muted);font-weight:400}
  .go-button{position:absolute;width:38px;height:38px;border-radius:50%;background:var(--yellow);display:flex;align-items:center;justify-content:center;box-shadow:0 6px 14px rgba(255,192,0,.35)}
  .social-bar{position:absolute;left:0;right:0;bottom:0;height:24px;background:var(--ink);color:var(--white);font:500 8px "Poppins",sans-serif;display:flex;align-items:center;justify-content:center;gap:5px;border-radius:0 0 38px 38px}
  .social-bar i{width:8px;height:8px;background:var(--white);border-radius:1px;display:block}
  .auth-title{position:absolute;font:italic 800 50px/1 "Poppins",sans-serif;color:var(--white)}
  .auth-title.ghost{color:#EEF0F4}

  .appbar{position:absolute;left:0;top:0;width:302px;background:var(--yellow);border-radius:0 0 46px 46px}
  .appbar-title{position:absolute;left:0;right:0;text-align:center;font:700 21px "Poppins",sans-serif;color:var(--white)}
  .back-arrow{position:absolute;left:14px}
  .avatar{position:absolute;right:16px;width:34px;height:34px;border-radius:50%;background:linear-gradient(135deg,#C9B49A,#6E6258);border:2px solid var(--white)}
  .avatar::after{content:"";position:absolute;right:-3px;top:-2px;width:8px;height:8px;border-radius:50%;background:#6BD16B;border:1.5px solid var(--white)}

  .device-row{position:absolute;left:15px;width:272px;height:72px;background:var(--white);border-radius:10px;box-shadow:0 10px 22px rgba(120,135,170,.14);display:flex;align-items:center;padding:0 14px;gap:14px}
  .device-icon{width:48px;height:48px;border-radius:50%;background:var(--yellow);display:flex;align-items:center;justify-content:center}
  .device-name{flex:1;font:600 14px "Poppins",sans-serif;color:var(--ink-soft)}
  .chevron{width:22px;height:22px;border-radius:50%;background:#EEF0F4;display:flex;align-items:center;justify-content:center}
  .chevron.solid{background:#A9AFBD}

  .form-heading{position:absolute;left:22px;font:600 13px "Poppins",sans-serif;color:var(--ink)}
  .options{position:absolute;left:22px;display:flex;gap:10px;font:500 7px "Poppins",sans-serif;color:var(--ink)}
  .options span{display:flex;align-items:center;gap:3px}
  .options span::before{content:"";width:6px;height:6px;border:1px solid var(--ink);border-radius:50%}
  .options .on{color:var(--yellow)}
  .options .on::before{background:var(--yellow);border-color:var(--yellow)}
  .divider{position:absolute;left:22px;right:22px;height:1px;background:var(--line)}
  .day-row{position:absolute;left:22px;display:flex;gap:8px}
  .day{width:42px;height:18px;border-radius:9px;background:#E8EAF0;font:600 7px/18px "Poppins",sans-serif;text-align:center;color:var(--ink)}
  .day.on{background:var(--yellow);color:var(--white)}
  .day.on::before{content:"✓ ";font-size:6px}
  .save-button{position:absolute;right:16px;width:82px;height:32px;border-radius:16px;background:var(--yellow);color:var(--white);font:700 11px/32px "Poppins",sans-serif;text-align:center;letter-spacing:.5px}

  .tabbar{position:absolute;left:0;right:0;bottom:0;height:64px;background:var(--white);display:flex;justify-content:space-around;align-items:flex-start;padding:10px 36px 0}
  .home-indicator{position:absolute;bottom:14px;left:50%;width:110px;height:4px;margin-left:-55px;border-radius:2px;background:#A9AFBD}

  .wave-box{position:absolute;left:22px;top:40px;width:176px;height:38px;border-radius:19px;background:#F2F3F7}
  .mic{position:absolute;width:40px;height:40px;border-radius:50%;background:var(--yellow);display:flex;align-items:center;justify-content:center}
</style>
</head>
<body>

<svg class="backdrop" viewBox="0 0 1200 3250" aria-hidden="true">
  <path d="M0 2660 C 260 2610 560 2680 760 2880 C 860 2980 900 3120 905 3250 L0 3250 Z" fill="var(--yellow-soft)"/>
</svg>

<div class="brand-title">varelko</div>

<!-- Splash -->
<div class="section-label" style="left:167px;top:308px">Splash</div>
<div class="screen" style="left:190px;top:395px">
  <div class="status"><span>9:41</span><span class="status-icons"><span style="width:10px;height:6px"></span><span style="width:8px;height:6px"></span><span style="width:14px;height:6px"></span></span></div>
  <svg class="abs" style="left:0;top:0" width="302" height="655" viewBox="0 0 302 655" aria-hidden="true">
    <rect width="302" height="655" fill="var(--yellow)"/>
    <path d="M0 364 C 60 320 130 300 190 305 C 240 310 280 335 302 360 L302 655 L0 655 Z" fill="var(--white)"/>
  </svg>
  <div class="abs" style="left:0;right:0;top:120px;text-align:center;font:600 58px/1 'Poppins',sans-serif;color:var(--white)">varelko</div>
</div>

<!-- Login -->
<div class="section-label" style="left:650px;top:484px">Login</div>
<div class="screen" style="left:674px;top:570px">
  <div class="status"><span>9:41</span><span class="status-icons"><span style="width:10px;height:6px"></span><span style="width:8px;height:6px"></span><span style="width:14px;height:6px"></span></span></div>
  <svg class="abs" style="left:0;top:0" width="302" height="220" aria-hidden="true"><path d="M0 0 H200 C 220 40 215 130 170 170 C 120 210 40 200 0 190 Z" fill="var(--yellow)"/></svg>
  <div class="auth-title" style="left:-4px;top:70px">Login</div>
  <div class="auth-title ghost" style="left:232px;top:70px">Sig</div>
  <div class="card" style="left:15px;top:177px;width:272px;height:197px">
    <div class="field" style="left:22px;top:42px;width:228px"><span>johndoe@postly.com</span><span class="hint">Email</span></div>
    <div class="field" style="left:22px;top:94px;width:228px"><span style="letter-spacing:1px">*********</span><span class="hint">Password</span></div>
  </div>
  <div class="go-button" style="left:130px;top:353px"><svg width="14" height="14" viewBox="0 0 14 14"><path d="M2 7h10M8 3l4 4-4 4" stroke="#fff" stroke-width="1.5" fill="none"/></svg></div>
  <div class="social-bar"><i></i>LINKBOOK</div>
</div>

<!-- Signup -->
<div class="section-label" style="left:167px;top:1215px">Signup</div>
<div class="screen" style="left:190px;top:1302px">
  <div class="status"><span>9:41</span><span class="status-icons"><span style="width:10px;height:6px"></span><span style="width:8px;height:6px"></span><span style="width:14px;height:6px"></span></span></div>
  <svg class="abs" style="left:0;top:0" width="302" height="260" aria-hidden="true"><path d="M0 0 H205 C 225 50 220 150 170 190 C 120 228 40 230 0 230 Z" fill="var(--yellow)"/></svg>
  <div class="auth-title" style="left:-2px;top:74px">Signup</div>
  <div class="auth-title ghost" style="left:232px;top:74px">Log</div>
  <div class="card" style="left:15px;top:175px;width:272px;height:305px">
    <div class="field" style="left:22px;top:42px;width:228px"><span>John</span><span class="hint">First Name</span></div>
    <div class="field" style="left:22px;top:94px;width:228px"><span>Doe</span><span class="hint">Last Name</span></div>
    <div class="field" style="left:22px;top:146px;width:228px"><span>johndoe@postly.com</span><span class="hint">Email</span></div>
    <div class="field" style="left:22px;top:198px;width:228px"><span style="letter-spacing:1px">*********</span><span class="hint">Password</span></div>
  </div>
  <div class="go-button" style="left:130px;top:459px"><svg width="14" height="14" viewBox="0 0 14 14"><path d="M2 7h10M8 3l4 4-4 4" stroke="#fff" stroke-width="1.5" fill="none"/></svg></div>
  <div class="social-bar"><i></i>LINKBOOK</div>
</div>

<!-- Dashboard -->
<div class="section-label" style="left:650px;top:1390px">Dashboard</div>
<div class="screen tinted" style="left:674px;top:1474px">
  <div class="status"><span>9:41</span><span class="status-icons"><span style="width:10px;height:6px"></span><span style="width:8px;height:6px"></span><span style="width:14px;height:6px"></span></span></div>
  <svg class="abs" style="left:0;top:0" width="302" height="230" aria-hidden="true">
    <path d="M0 0 H302 V110 C 290 135 270 140 230 140 H70 C 30 140 10 130 0 100 Z" fill="var(--yellow)"/>
    <path d="M40 140 C 70 210 200 230 230 160 Z" fill="var(--yellow)"/>
  </svg>
  <div class="appbar-title" style="top:60px">Dashboard</div>
  <div class="avatar" role="img" aria-label="User profile photo" style="top:60px"></div>

  <div class="device-row" style="top:126px">
    <div class="device-icon"><svg width="28" height="18" viewBox="0 0 28 18"><rect x="1" y="1" width="26" height="16" rx="3" fill="none" stroke="#fff" stroke-width="1.6"/><rect x="5" y="5" width="5" height="8" fill="none" stroke="#fff" stroke-width="1.2"/><rect x="12" y="5" width="5" height="8" fill="none" stroke="#fff" stroke-width="1.2"/><rect x="19" y="5" width="4" height="8" fill="none" stroke="#fff" stroke-width="1.2"/></svg></div>
    <div class="device-name">Timers</div>
    <div class="chevron solid"><svg width="8" height="8" viewBox="0 0 8 8"><path d="M3 1l3 3-3 3" stroke="#fff" stroke-width="1.2" fill="none"/></svg></div>
  </div>
  <div class="device-row" style="top:223px">
    <div class="device-icon"><svg width="24" height="20" viewBox="0 0 24 20"><path d="M2 7h4l6-5v16l-6-5H2z" fill="#fff"/><path d="M15 6c2 2 2 6 0 8M18 3c4 4 4 10 0 14" stroke="#fff" stroke-width="1.6" fill="none"/></svg></div>
    <div class="device-name">Speakers</div>
    <div class="chevron"><svg width="8" height="8" viewBox="0 0 8 8"><path d="M3 1l3 3-3 3" stroke="#A9AFBD" stroke-width="1.2" fill="none"/></svg></div>
  </div>
  <div class="device-row" style="top:320px">
    <div class="device-icon"><svg width="24" height="22" viewBox="0 0 24 22"><path d="M6 18v-7a6 6 0 0112 0v7z" fill="#fff"/><rect x="3" y="18" width="18" height="3" rx="1" fill="#fff"/><path d="M12 1v3M3 5l2 2M21 5l-2 2" stroke="#fff" stroke-width="1.6"/></svg></div>
    <div class="device-name">Motorized Siren</div>
    <div class="chevron"><svg width="8" height="8" viewBox="0 0 8 8"><path d="M3 1l3 3-3 3" stroke="#A9AFBD" stroke-width="1.2" fill="none"/></svg></div>
  </div>

  <svg class="abs" style="left:0;top:500px" width="302" height="100" aria-hidden="true">
    <circle cx="175" cy="78" r="42" fill="var(--yellow-soft)"/>
    <circle cx="255" cy="95" r="70" fill="var(--yellow)"/>
    <circle cx="212" cy="90" r="28" fill="none" stroke="var(--yellow-pale)" stroke-width="5"/>
  </svg>
  <div class="tabbar">
    <svg width="18" height="18" viewBox="0 0 18 18"><path d="M2 9L9 2l7 7v7H11v-5H7v5H2z" fill="var(--yellow)"/></svg>
    <svg width="18" height="18" viewBox="0 0 18 18"><circle cx="9" cy="9" r="8" fill="#A9AFBD"/><path d="M9 5v8M5 9h8" stroke="#fff" stroke-width="1.6"/></svg>
    <svg width="18" height="18" viewBox="0 0 18 18"><path d="M4 13V8a5 5 0 0110 0v5l1.5 1.5h-13z" fill="#A9AFBD"/><circle cx="9" cy="16" r="1.6" fill="#A9AFBD"/></svg>
    <svg width="18" height="18" viewBox="0 0 18 18"><circle cx="9" cy="9" r="6" fill="none" stroke="#A9AFBD" stroke-width="3.5" stroke-dasharray="2.4 2.3"/><circle cx="9" cy="9" r="4.5" fill="none" stroke="#A9AFBD" stroke-width="2"/></svg>
  </div>
  <div class="home-indicator"></div>
</div>

<!-- Timer -->
<div class="section-label" style="left:167px;top:2120px">Timer</div>
<div class="screen tinted" style="left:159px;top:2208px">
  <div class="appbar" style="height:113px"></div>
  <div class="status"><span>9:41</span><span class="status-icons"><span style="width:10px;height:6px"></span><span style="width:8px;height:6px"></span><span style="width:14px;height:6px"></span></span></div>
  <svg class="back-arrow" style="top:70px" width="10" height="14" viewBox="0 0 10 14"><path d="M8 1L2 7l6 6" stroke="#fff" stroke-width="2" fill="none"/></svg>
  <div class="appbar-title" style="top:58px">Timer</div>
  <div class="avatar" role="img" aria-label="User profile photo" style="top:58px"></div>

  <div class="card" style="left:15px;top:111px;width:272px;height:236px">
    <div class="form-heading" style="top:16px">Select Device</div>
    <div class="field" style="left:22px;top:46px;width:228px"><span>Select</span><svg width="9" height="6" viewBox="0 0 9 6"><path d="M1 1l3.5 3.5L8 1" stroke="#7A8194" fill="none"/></svg></div>
    <div class="form-heading" style="top:98px">Activation Timer</div>
    <div class="field" style="left:22px;top:128px;width:110px"><span>Start Date</span><svg width="10" height="10" viewBox="0 0 10 10"><rect x=".5" y="1.5" width="9" height="8" fill="none" stroke="#B5BAC6"/></svg></div>
    <div class="field" style="left:138px;top:128px;width:112px"><span>End Date</span><svg width="10" height="10" viewBox="0 0 10 10"><rect x=".5" y="1.5" width="9" height="8" fill="none" stroke="#B5BAC6"/></svg></div>
    <div class="field" style="left:22px;top:177px;width:228px"><span>Select Time</span><svg width="10" height="10" viewBox="0 0 10 10"><circle cx="5" cy="5" r="4.3" fill="none" stroke="#B5BAC6"/><path d="M5 2.5V5h2" stroke="#B5BAC6" fill="none"/></svg></div>
  </div>

  <div class="card" style="left:15px;top:357px;width:272px;height:160px">
    <div class="form-heading" style="top:14px">Repeat Activation</div>
    <div class="options" style="top:42px"><span>Only Once</span><span>Daily</span><span>Weekly</span><span class="on">Custom Input</span></div>
    <div class="divider" style="top:62px"></div>
    <div class="day-row" style="top:92px"><span class="day on">MON</span><span class="day on">TUE</span><span class="day">WED</span><span class="day on">THU</span></div>
    <div class="day-row" style="top:118px"><span class="day">FRI</span><span class="day">SAT</span><span class="day">SUN</span></div>
  </div>
  <div class="save-button" style="top:527px">SAVE</div>

  <div class="tabbar" style="background:transparent">
    <svg width="18" height="18" viewBox="0 0 18 18"><path d="M2 9L9 2l7 7v7H11v-5H7v5H2z" fill="var(--yellow)"/></svg>
    <svg width="18" height="18" viewBox="0 0 18 18"><circle cx="9" cy="9" r="8" fill="#A9AFBD"/><path d="M9 5v8M5 9h8" stroke="#fff" stroke-width="1.6"/></svg>
    <svg width="18" height="18" viewBox="0 0 18 18"><path d="M4 13V8a5 5 0 0110 0v5l1.5 1.5h-13z" fill="#A9AFBD"/><circle cx="9" cy="16" r="1.6" fill="#A9AFBD"/></svg>
    <svg width="18" height="18" viewBox="0 0 18 18"><circle cx="9" cy="9" r="6" fill="none" stroke="#A9AFBD" stroke-width="3.5" stroke-dasharray="2.4 2.3"/><circle cx="9" cy="9" r="4.5" fill="none" stroke="#A9AFBD" stroke-width="2"/></svg>
  </div>
  <div class="home-indicator"></div>
</div>

<!-- Speakers -->
<div class="section-label" style="left:650px;top:2297px">Speakers</div>
<div class="screen tinted" style="left:674px;top:2383px">
  <div class="appbar" style="height:110px"></div>
  <div class="status"><span>9:41</span><span class="status-icons"><span style="width:10px;height:6px"></span><span style="width:8px;height:6px"></span><span style="width:14px;height:6px"></span></span></div>
  <svg class="back-arrow" style="top:68px" width="10" height="14" viewBox="0 0 10 14"><path d="M8 1L2 7l6 6" stroke="#fff" stroke-width="2" fill="none"/></svg>
  <div class="appbar-title" style="top:56px">Speakers</div>
  <div class="avatar" role="img" aria-label="User profile photo" style="top:56px"></div>

  <div class="card" style="left:15px;top:110px;width:272px;height:236px">
    <div class="form-heading" style="top:16px">Select Device</div>
    <div class="field" style="left:22px;top:46px;width:228px"><span>Select</span><svg width="9" height="6" viewBox="0 0 9 6"><path d="M1 1l3.5 3.5L8 1" stroke="#7A8194" fill="none"/></svg></div>
    <div class="form-heading" style="top:98px">Activation Timer</div>
    <div class="field" style="left:22px;top:128px;width:110px"><span>Start Date</span><svg width="10" height="10" viewBox="0 0 10 10"><rect x=".5" y="1.5" width="9" height="8" fill="none" stroke="#B5BAC6"/></svg></div>
    <div class="field" style="left:138px;top:128px;width:112px"><span>End Date</span><svg width="10" height="10" viewBox="0 0 10 10"><rect x=".5" y="1.5" width="9" height="8" fill="none" stroke="#B5BAC6"/></svg></div>
    <div class="field" style="left:22px;top:177px;width:228px"><span>Select Time</span><svg width="10" height="10" viewBox="0 0 10 10"><circle cx="5" cy="5" r="4.3" fill="none" stroke="#B5BAC6"/><path d="M5 2.5V5h2" stroke="#B5BAC6" fill="none"/></svg></div>
  </div>

  <div class="card" style="left:15px;top:362px;width:272px;height:110px">
    <div class="form-heading" style="top:14px">Audio Configuration</div>
    <div class="options" style="top:38px"><span class="on">Record Voice</span><span>Text to Speech</span></div>
    <div class="wave-box" style="top:56px">
      <svg width="176" height="38" viewBox="0 0 176 38" aria-hidden="true">
        <g stroke="#6B7387" stroke-width="1.3">
          <path d="M16 15v8M20 12v14M24 16v6M28 9v20M32 13v12M36 17v4M40 10v18M44 14v10M48 7v24M52 12v14M56 16v6M60 11v16M64 14v10"/>
        </g>
        <g stroke="#B9BECA" stroke-width="1.3">
          <path d="M68 12v14M72 16v6M76 10v18M80 14v10M84 9v20M88 15v8M92 12v14M96 17v4M100 11v16M104 14v10M108 9v20M112 13v12M116 16v6M120 12v14M124 15v8M128 10v18M132 14v10M136 16v6M140 12v14M144 15v8M148 17v4M152 13v12M156 16v6"/>
        </g>
        <path d="M64 6v26" stroke="var(--ink)" stroke-width="1.5"/>
      </svg>
    </div>
    <div class="mic" style="left:206px;top:55px"><svg width="14" height="20" viewBox="0 0 14 20"><rect x="4" y="1" width="6" height="11" rx="3" fill="#fff"/><path d="M1.5 9a5.5 5.5 0 0011 0M7 14.5V19" stroke="#fff" stroke-width="1.5" fill="none"/></svg></div>
  </div>

  <div class="card" style="left:15px;top:488px;width:272px;height:110px">
    <div class="form-heading" style="top:14px">Repeat Activation</div>
    <div class="options" style="top:42px"><span>Only Once</span><span>Daily</span><span>Weekly</span><span class="on">Custom Input</span></div>
  </div>

  <div class="tabbar">
    <svg width="18" height="18" viewBox="0 0 18 18"><path d="M2 9L9 2l7 7v7H11v-5H7v5H2z" fill="var(--yellow)"/></svg>
    <svg width="18" height="18" viewBox="0 0 18 18"><circle cx="9" cy="9" r="8" fill="#A9AFBD"/><path d="M9 5v8M5 9h8" stroke="#fff" stroke-width="1.6"/></svg>
    <svg width="18" height="18" viewBox="0 0 18 18"><path d="M4 13V8a5 5 0 0110 0v5l1.5 1.5h-13z" fill="#A9AFBD"/><circle cx="9" cy="16" r="1.6" fill="#A9AFBD"/></svg>
    <svg width="18" height="18" viewBox="0 0 18 18"><circle cx="9" cy="9" r="6" fill="none" stroke="#A9AFBD" stroke-width="3.5" stroke-dasharray="2.4 2.3"/><circle cx="9" cy="9" r="4.5" fill="none" stroke="#A9AFBD" stroke-width="2"/></svg>
  </div>
  <div class="home-indicator"></div>
</div>

</body>
</html>
```